business card for horse saddlery

after a new business card for our saddlery, i will add 2 logos we have previously used and they can be used (or not) . Any images can be used from our website also at www.harrowfields.net.au, I have also added our brand logo, which may be good to incorporate on back ? we have over 15, 000 items online, ship Australia Wide.

Target Market(s)

horse owners

Industry/Entity Type

Retail - Equestrian

Contact Information for Business Card

Harrowfield Horse Supplies, 1300 48 62 90, www.harrowfields.net.au, 27 Lindqvist Rd Marrowbank Q 4587

Requirements
Must have
• trailgem is our brand so trailgem logo on back as 'distributers of', easy to read
Nice to have
• professional but fun
Should not have
• double sided (description wont save double sided)

```html
<!DOCTYPE html>
<html lang="en">
<head>
<meta charset="utf-8">
<title>Harrowfield Horse Supplies – Business Card</title>
<link rel="stylesheet" href="https://fonts.googleapis.com/css2?family=Open+Sans:wght@400;600;700&display=swap">
<style>
  :root {
    --stage: #232323;
    --paper: #ffffff;
    --navy: #2b3f80;
    --orange: #fbb01e;
    --ink: #111111;
    --icon-blue: #3a78c9;
    --photo-dark: #0d0d0d;
    --photo-light: #cfcfcf;
  }
  * { box-sizing: border-box; margin: 0; padding: 0; }
  html, body {
    width: 1200px; height: 780px; overflow: hidden;
    background: var(--stage);
    font-family: "Open Sans", Arial, sans-serif;
  }
  .card {
    position: absolute; left: 75px; top: 90px;
    width: 1050px; height: 600px;
    background: var(--paper);
    border-radius: 44px;
    border-bottom: 7px solid var(--orange);
    border-left: 3px solid var(--orange);
    overflow: hidden;
  }
  .card-waves { position: absolute; inset: 0; width: 100%; height: 100%; }

  .partner-marks {
    position: absolute; left: 60px; top: 70px;
    display: flex; gap: 44px; align-items: center;
  }
  .partner-mark { display: flex; align-items: center; gap: 10px; font-size: 24px; font-weight: 600; }
  .partner-mark .dot { width: 26px; height: 26px; border-radius: 50%; }
  .partner-mark--web { color: var(--icon-blue); }
  .partner-mark--web .dot { background: var(--icon-blue); }
  .partner-mark--brand { color: var(--navy); text-transform: uppercase; letter-spacing: 2px; }
  .partner-mark--brand .dot { background: var(--navy); }

  .brand-mark {
    position: absolute; right: 60px; top: 60px;
    display: flex; align-items: center; gap: 16px;
    color: var(--navy); font-weight: 700; font-size: 34px; line-height: 1.1;
    width: 400px;
  }
  .brand-mark .sun { flex: none; width: 70px; height: 70px; border-radius: 50%; background: var(--orange); }

  .holder {
    position: absolute; left: 60px; top: 250px;
    border-left: 16px solid var(--orange);
    padding-left: 18px;
  }
  .holder-name { font-size: 54px; font-weight: 700; line-height: 1.05; }
  .holder-name .first { color: var(--orange); }
  .holder-name .last { color: var(--navy); }
  .holder-role { font-size: 27px; font-weight: 600; color: var(--ink); margin-top: 4px; }

  .contact-list { position: absolute; left: 80px; top: 395px; list-style: none; }
  .contact-item {
    display: flex; align-items: center; gap: 14px;
    color: var(--ink); font-size: 26px; font-weight: 600; height: 40px;
  }
  .contact-item--phone { font-size: 36px; font-weight: 700; height: 50px; }
  .contact-icon {
    width: 30px; height: 30px; border-radius: 50%;
    background: var(--icon-blue); border: 2px solid var(--orange);
    display: flex; align-items: center; justify-content: center; flex: none;
  }

  .horse-photo {
    position: absolute; left: 725px; top: 168px;
    width: 300px; height: 300px; border-radius: 50%;
    border: 7px solid var(--orange);
    background: radial-gradient(circle at 45% 45%, var(--photo-light) 0%, #8a8a8a 30%, var(--photo-dark) 65%);
  }
</style>
</head>
<body>
  <section class="card">
    <svg class="card-waves" viewBox="0 0 1050 600" preserveAspectRatio="none" aria-hidden="true">
      <path d="M150,575 C470,555 760,470 880,375 C940,330 990,300 1050,290 L1050,320 C990,330 950,355 895,395 C770,490 480,575 150,590 Z" fill="var(--orange)"/>
      <path d="M230,600 C520,585 790,500 900,410 C960,365 1000,345 1050,335 L1050,600 Z" fill="var(--navy)"/>
    </svg>

    <div class="partner-marks">
      <div class="partner-mark partner-mark--web"><span class="dot"></span>harrowfields.net.au</div>
      <div class="partner-mark partner-mark--brand"><span class="dot"></span>Trailgem</div>
    </div>

    <div class="brand-mark">
      <span class="sun"></span>
      <span>Harrowfield Horse Supplies</span>
    </div>

    <div class="horse-photo" role="img" aria-label="Photo of a grey horse wearing a halter on a black background"></div>

    <div class="holder">
      <h1 class="holder-name"><span class="first">Milena</span> <span class="last">Varga</span></h1>
      <p class="holder-role">Horse owners</p>
    </div>

    <ul class="contact-list">
      <li class="contact-item contact-item--phone">
        <span class="contact-icon"><svg width="16" height="16" viewBox="0 0 24 24"><path d="M6.6 10.8c1.4 2.8 3.8 5.1 6.6 6.6l2.2-2.2c.3-.3.7-.4 1-.2 1.1.4 2.3.6 3.6.6.6 0 1 .4 1 1V20c0 .6-.4 1-1 1C10.6 21 3 13.4 3 4c0-.6.4-1 1-1h3.5c.6 0 1 .4 1 1 0 1.3.2 2.5.6 3.6.1.3 0 .7-.2 1z" fill="#fff"/></svg></span>
        1300 48 62 90
      </li>
      <li class="contact-item">
        <span class="contact-icon"><svg width="16" height="16" viewBox="0 0 24 24" fill="none" stroke="#fff" stroke-width="2"><circle cx="12" cy="12" r="9"/><path d="M3 12h18M12 3c3 3 3 15 0 18M12 3c-3 3-3 15 0 18"/></svg></span>
        www.harrowfields.net.au
      </li>
      <li class="contact-item">
        <span class="contact-icon"><svg width="16" height="16" viewBox="0 0 24 24"><path d="M12 2a7 7 0 0 0-7 7c0 5 7 13 7 13s7-8 7-13a7 7 0 0 0-7-7zm0 9.5A2.5 2.5 0 1 1 12 6.5a2.5 2.5 0 0 1 0 5z" fill="#fff"/></svg></span>
        27 Lindqvist Rd Marrowbank Q 4587
      </li>
    </ul>
  </section>
</body>
</html>
```